Surgical Conditions of the thyroid and parathyroid glands - a flyer for GPs

Hi there,

I am a thyroid surgeon trying to produce a bi-fold A4 flyer as a quick reference guide for general practitioners (family doctors). It needs to feel friendly and professional.

The text for the four "pages" can be found in the "thyroid flyer for design" document attached.

The front page should have:
- The title
- the photo with the patient having an ultrasound
- the photo of the asian woman with the enlarged thyroid gland
- possibly the photo of the blonde woman touching her neck

The inner two pages are predominantly text - I would love this to be presented in an easy to read, uncluttered format. There is a photo attached which demonstrates the parathyroid glands. This should be placed near the parathyroid text section if possible.

The back page is a brief bio of myself. It should have the profile pic attached.
It should have contact details, which I forgot to put in the word document. These details are:
Phone (03) 9418 2057 for all appointments
Consulting at:
27 Tollard Crescent, Berwick, VIC 3806
marlowsurgicalclinic.com.au
dovilatremont.com

The back page should also have the "Fenwick Care" and "Guild of Operators" logos.

If possible, all pages should have the "Marlow Surgical Clinic" logo.

The whole feel could have a similar colour scheme to my group website (largely orange and green). Please see www.marlowsurgicalclinic.com.au for examples.

Many thanks!

Target Market(s)

General practitioners (ie family doctors)

Industry/Entity Type

Medical And Science

Font styles to use
Sans Serif

Colors
33b8a4
f78f20

Requirements
Must have
• Contact details on the back, marlow surgical clinic logo on front and back pages, Fenwick Care and Guild of Operators logo on the back.
Nice to have
• Other medical/surgical related images as you see fit - sorry to be so broad!!

```html
<!DOCTYPE html>
<html lang="en">
<head>
<meta charset="utf-8">
<title>Surgical Conditions of the Thyroid – GP Quick Reference</title>
<link href="https://fonts.googleapis.com/css2?family=Lato:ital,wght@0,400;0,700;0,900;1,700;1,900&display=swap" rel="stylesheet">
<style>
:root{
  --backdrop:#5a5a5a;
  --paper:#ffffff;
  --mint:#e6f4f0;
  --mint-soft:#eef8f5;
  --green:#17a085;
  --green-band:#1fa585;
  --orange:#f26522;
  --gold:#f5a623;
  --ink:#3a3a3a;
  --grey:#6b6b6b;
}
*{margin:0;padding:0;box-sizing:border-box}
html,body{width:1200px;height:867px;overflow:hidden}
body{background:var(--backdrop);font-family:'Lato',sans-serif;color:var(--ink);position:relative}
.page{position:absolute;top:60px;height:745px;width:528px;overflow:hidden}
.page--left{left:72px;background:var(--paper)}
.page--right{left:600px;background:var(--mint-soft)}
.abs{position:absolute}
.silhouette{position:absolute;left:0;top:160px;width:528px;height:585px;background:linear-gradient(180deg,var(--mint-soft),var(--mint));clip-path:polygon(0 40%,12% 36%,18% 20%,26% 0,74% 0,82% 20%,88% 36%,100% 40%,100% 100%,0 100%)}
.page-title{font-weight:900;font-size:26px;color:var(--green);letter-spacing:.2px;white-space:nowrap}
.section-title{font-weight:900;font-size:19.5px;color:var(--green);white-space:nowrap}
.disorder h3{font-weight:900;font-size:11px;color:var(--orange);text-transform:uppercase;margin-bottom:1px}
.disorder p{font-size:11.2px;line-height:13.6px;color:var(--ink)}
.disorder{margin-bottom:12px}
.symptom-bar{position:absolute;left:128px;width:236px;height:19px;background:var(--orange);color:#fff;font-weight:900;font-size:11.5px;text-align:center;line-height:19px;text-transform:uppercase}
.symptom{position:absolute;width:90px;text-align:center}
.symptom .figure{display:block;width:26px;height:50px;margin:0 auto 5px;background:var(--green);border-radius:13px 13px 4px 4px;opacity:.9}
.symptom span{font-weight:700;font-size:11px;color:#222;white-space:nowrap}
.design-note{position:absolute;left:446px;top:683px;width:68px;font-size:8.5px;font-weight:700;line-height:13px;text-align:center;color:#222}
.workup-band{position:absolute;left:0;top:68px;width:528px;height:252px;background:var(--green-band)}
.workup-text{position:absolute;left:40px;top:78px;width:268px;color:#fff;font-size:11px;line-height:13.7px}
.workup-text p{margin-bottom:11px}
.workup-text b{font-style:italic;font-weight:900}
.photo-ring{position:absolute;border-radius:50%;border:6px solid #fff}
.photo--test{left:332px;top:54px;width:186px;height:186px;box-shadow:0 0 0 5px var(--gold);background:radial-gradient(circle at 45% 40%,#f3f4f7,#c9cfe0 60%,#8fa0c9)}
.photo--gland{left:326px;top:240px;width:162px;height:162px;box-shadow:0 0 0 4px var(--green-band);background:radial-gradient(circle at 50% 45%,#fbe9e6,#e6d8d6 55%,#b9c4c6)}
.fna-title{position:absolute;left:36px;top:344px;font-weight:900;font-size:18px;line-height:19px;color:var(--green)}
.fna-list{position:absolute;left:36px;top:397px;width:264px}
.fna-list h4{font-weight:900;font-size:15px;color:var(--green);margin-bottom:2px}
.fna-list ul{list-style:none;margin-bottom:9px}
.fna-list li{position:relative;padding-left:13px;font-size:11px;line-height:13.6px;margin-bottom:2px}
.fna-list li::before{content:"";position:absolute;left:1px;top:3px;border-left:7px solid var(--orange);border-top:4px solid transparent;border-bottom:4px solid transparent}
.divider{position:absolute;left:320px;top:392px;width:1px;height:283px;background:#888}
.parathyroid{position:absolute;left:340px;top:415px;width:150px}
.parathyroid h3{font-weight:900;font-size:18px;line-height:19px;color:var(--green);margin-bottom:10px}
.parathyroid p{font-size:11px;line-height:13.7px}
.parathyroid b{font-style:italic;font-weight:900}
.brand{position:absolute;left:380px;top:622px;width:130px;display:flex;flex-direction:column;align-items:center;gap:6px}
.brand-mark{width:36px;height:36px;border-radius:50%;background:var(--orange)}
.brand-name{font-weight:900;font-size:13px;line-height:15px;color:var(--grey);text-align:center}
.site-url{position:absolute;left:155px;top:705px;font-size:13px;color:var(--grey)}
.site-url b{font-weight:900}
</style>
</head>
<body>

<section class="page page--left">
  <div class="silhouette" role="img" aria-label="Faint head-and-shoulders silhouette behind the symptom list"></div>

  <h1 class="page-title abs" style="left:39px;top:24px">COMMON THYROID DISORDERS</h1>

  <div class="abs" style="left:43px;top:65px;width:170px">
    <div class="disorder"><h3>Solitary nodules</h3><p>often require characterisation with ultrasound +/- fine needle aspirate to determine likelihood of malignancy</p></div>
    <div class="disorder"><h3>Multinodular goitre</h3><p>usually benign but may cause compressive symptoms</p></div>
    <div class="disorder"><h3>Graves’ disease</h3><p>autoimmune stimulation of TSH receptors leading to hyperthyroidism</p></div>
  </div>
  <div class="abs" style="left:229px;top:63px;width:248px">
    <div class="disorder"><h3>Thyroid cancer</h3><p>important risk factors include family history and a history of radiation exposure. Readily treatable with surgery, often in conjunction with radioactive iodine</p></div>
    <div class="disorder"><h3>Hashimoto’s thyroiditis</h3><p>usually self-limiting, can cause hyperthyroidism (early) or hypothyroidism (late). May benefit from surgery if associated with ongoing pain</p></div>
    <div class="disorder"><h3>Thyroglossal cyst</h3><p>presents as a midline lump above the thyroid cartilage (Adam’s apple), may become inflamed or form fistulas to the overlying skin</p></div>
  </div>

  <h2 class="section-title abs" style="left:43px;top:283px">COMMON SYMPTOMS OF THYROID DISEASE</h2>

  <div class="symptom-bar" style="top:313px">Symptoms of hyperthyroidism</div>
  <div class="symptom" style="left:58px;top:345px"><i class="figure" role="img" aria-label="Pictogram of a person feeling hot"></i><span>Heat intolerance</span></div>
  <div class="symptom" style="left:145px;top:345px"><i class="figure" role="img" aria-label="Pictogram of a tired person"></i><span>Tiredness</span></div>
  <div class="symptom" style="left:225px;top:345px"><i class="figure" role="img" aria-label="Pictogram of a person with palpitations"></i><span>Palpitations</span></div>
  <div class="symptom" style="left:296px;top:345px"><i class="figure" role="img" aria-label="Pictogram of a person with tremor"></i><span>Tremor</span></div>
  <div class="symptom" style="left:363px;top:345px"><i class="figure" role="img" aria-label="Pictogram of a sweating person"></i><span>Sweats</span></div>

  <div class="symptom" style="left:73px;top:430px"><i class="figure" role="img" aria-label="Pictogram of a person with bulging eyes"></i><span>exophthalmos</span></div>
  <div class="symptom" style="left:162px;top:430px"><i class="figure" role="img" aria-label="Pictogram of a person with diarrhoea"></i><span>Diarrhoea</span></div>
  <div class="symptom" style="left:243px;top:430px"><i class="figure" role="img" aria-label="Pictogram of a person losing weight"></i><span>Weight loss</span></div>
  <div class="symptom" style="left:323px;top:430px"><i class="figure" role="img" aria-label="Pictogram of a person with heavy periods"></i><span>Menorrhagia</span></div>

  <div class="symptom-bar" style="top:512px">Symptoms of hypothyroidism</div>
  <div class="symptom" style="left:48px;top:543px"><i class="figure" role="img" aria-label="Pictogram of a person asleep at a desk"></i><span>Lethargy</span></div>
  <div class="symptom" style="left:128px;top:543px"><i class="figure" role="img" aria-label="Pictogram of a person gaining weight"></i><span>Weight gain</span></div>
  <div class="symptom" style="left:213px;top:543px"><i class="figure" role="img" aria-label="Pictogram of a weak, stooping person"></i><span>Weakness</span></div>
  <div class="symptom" style="left:273px;top:543px"><i class="figure" role="img" aria-label="Pictogram of a person feeling cold"></i><span>Cold</span></div>
  <div class="symptom" style="left:348px;top:543px"><i class="figure" role="img" aria-label="Pictogram of a person losing hair"></i><span>Hair loss</span></div>

  <div class="symptom-bar" style="top:624px">Compressive symptoms</div>
  <div class="symptom" style="left:58px;top:655px"><i class="figure" role="img" aria-label="Pictogram of a person with difficulty swallowing"></i><span>Dysphagia</span></div>
  <div class="symptom" style="left:143px;top:655px"><i class="figure" role="img" aria-label="Pictogram of a person short of breath"></i><span>Dyspnoea</span></div>
  <div class="symptom" style="left:238px;top:655px"><i class="figure" role="img" aria-label="Pictogram of a person with a neck lump"></i><span>Lump in the neck</span></div>
  <div class="symptom" style="left:343px;top:655px"><i class="figure" role="img" aria-label="Pictogram of a person with a hoarse voice"></i><span>Voice change</span></div>

  <p class="design-note">If you like the design i will create remaing icons</p>
</section>

<section class="page page--right">
  <h1 class="page-title abs" style="left:36px;top:22px">WORKUP FOR THYROID DISORDERS</h1>

  <div class="workup-band"></div>
  <div class="workup-text">
    <p>Most thyroid disorders requiring surgical intervention can be diagnosed with a <b>thyroid ultrasound</b> and <b>thyroid function tests.</b></p>
    <p>If a patient is biochemically hyperthyroid, a <b>thyroid nuclear scan</b>and <b>anti-TSH receptor antibodies</b> are useful to determine the underlying cause (eg Graves’ disease, toxic nodule or toxic goitre). <b>Thyroid antibodies</b> can also determine if there is underlying thyroiditis. All patients with thyroid disease should also undergo screening for concurrent parathyroid disease with <b style="font-style:normal">PTH</b>,<b style="font-style:normal">calcium</b> and <b>vitamin D</b> levels.</p>
    <p>A nodule with suspicious features on ultrasound (increased vascularity, microcalcifications, irregular border) should <b>undergo ultrasound-guided fine needle aspirate.</b></p>
  </div>

  <div class="photo-ring photo--test" role="img" aria-label="Photo of a gloved hand holding a thyroid test blood tube"></div>
  <div class="photo-ring photo--gland" role="img" aria-label="Medical illustration of the thyroid with parathyroid glands highlighted"></div>

  <h2 class="fna-title">Which nodules should<br>undergo fine needle aspirate?</h2>

  <div class="fna-list">
    <h4>Nodules &lt;1 cm</h4>
    <ul>
      <li>If there are suspicious features on ultrasound (irregular border, microcalcifications, increased vascularity)</li>
      <li>Nodules without suspicious features less than 1 cm can be re-evaluated with an ultrasound in 1 year</li>
    </ul>
    <h4>Nodules 1 to 3 cm</h4>
    <ul>
      <li>Should undergo FNA, especially if there are suspicious features</li>
    </ul>
    <h4>Nodules &gt;3cm</h4>
    <ul>
      <li>Should undergo FNA</li>
      <li>These nodules are more likely to become symptomatic and there is an increased risk of a false negative FNA with nodules of this size. They should therefore be considered for excision via a hemithyroidectomy. An FNA can determine if a total thyroidectomy is preferred in the case of malignancy.</li>
    </ul>
  </div>

  <div class="divider"></div>

  <div class="parathyroid">
    <h3>Parathyroid<br>disease</h3>
    <p>Simple screening with <b>calcium</b> and <b>PTH</b> levels can detect hyperparathyroidism before symptoms become evident. Patients with osteoporosis, recurrent kidney stones or pathological fractures should be tested, as well as with an <b>ultrasound</b> to look for concurrent thyroid issues.</p>
  </div>

  <div class="brand"><span class="brand-mark"></span><span class="brand-name">MARLOW<br>SURGICAL CLINIC</span></div>

  <p class="site-url">www.<b>marlowsurgical</b>clinic.com.au</p>
</section>

</body>
</html>
```